Letterhead and business card design

We have recently had a logo designed by brandnestly. now we need a corporate identity with business card and lettehead design.

Target Market(s)

law firms corporates

Industry/Entity Type

Business

Requirements
Should not have
• cheesy detecive stuff like magnifying glasses etxcc

```html
<!DOCTYPE html>
<html lang="en">
<head>
<meta charset="utf-8">
<title>Halbrook &amp; Vane — Business Card</title>
<link rel="stylesheet" href="https://fonts.googleapis.com/css2?family=Cormorant+Garamond:ital,wght@1,500&family=Questrial&display=swap">
<style>
  :root {
    --backdrop: #e6e6e4;
    --card-front: #fbfbfa;
    --card-back: #8f9290;
    --ink: #5b5c5c;
    --ink-soft: #6e6f6f;
    --ink-light: #f4f4f2;
    --ink-light-soft: #dcdedd;
  }
  * { box-sizing: border-box; margin: 0; padding: 0; }
  html, body { width: 1200px; height: 800px; overflow: hidden; }
  body {
    background: var(--backdrop);
    font-family: "Questrial", "Century Gothic", sans-serif;
    display: flex;
    align-items: center;
    justify-content: center;
    gap: 60px;
  }
  .card {
    position: relative;
    width: 520px;
    height: 297px;
    box-shadow: 0 6px 18px rgba(0,0,0,0.18);
  }
  .card--front { background: var(--card-front); color: var(--ink); }
  .card--back { background: var(--card-back); color: var(--ink-light); }

  .brand {
    position: absolute;
    left: 0; right: 0;
    text-align: center;
  }
  .card--front .brand { top: 62px; }
  .card--back .brand { top: 92px; }
  .brand__name {
    font-family: "Questrial", "Century Gothic", sans-serif;
    font-size: 34px;
    letter-spacing: 3px;
    text-transform: uppercase;
    line-height: 1;
  }
  .brand__tagline {
    margin-top: 10px;
    font-family: "Cormorant Garamond", Georgia, serif;
    font-style: italic;
    font-weight: 500;
    font-size: 16px;
    letter-spacing: 0.5px;
  }
  .card--back .brand__tagline { color: var(--ink-light-soft); }

  .contact {
    position: absolute;
    left: 26px; right: 26px;
    bottom: 24px;
    display: flex;
    justify-content: space-between;
    align-items: flex-end;
    font-size: 12px;
    line-height: 1.45;
    color: var(--ink-soft);
  }
  .contact__list { list-style: none; }
  .contact__item { display: flex; align-items: center; gap: 6px; }
  .contact__icon { width: 11px; height: 11px; flex: none; }

  .holder {
    position: absolute;
    left: 0; right: 0;
    top: 200px;
    text-align: center;
    line-height: 1.3;
  }
  .holder__name { font-size: 15px; letter-spacing: 1px; text-transform: uppercase; }
  .holder__title { font-size: 12px; color: var(--ink-light-soft); }
</style>
</head>
<body>

  <article class="card card--front">
    <div class="brand">
      <div class="brand__name">Halbrook &amp; Vane</div>
      <div class="brand__tagline">Investigations • Security • Intelligence</div>
    </div>

    <div class="contact">
      <address class="contact__address" style="font-style: normal;">
        PO Box 318, Harbour Lane<br>
        Wellford, New Zealand
      </address>

      <ul class="contact__list">
        <li class="contact__item">
          <svg class="contact__icon" viewBox="0 0 12 12" fill="none" stroke="currentColor" stroke-width="1.2"><rect x="1" y="2.5" width="10" height="7"/><path d="M1 2.5 6 6.5 11 2.5"/></svg>
          marcus@vaneinquiries.co.nz
        </li>
        <li class="contact__item">
          <svg class="contact__icon" viewBox="0 0 12 12" fill="none" stroke="currentColor" stroke-width="1"><circle cx="6" cy="6" r="5"/><ellipse cx="6" cy="6" rx="2.2" ry="5"/><path d="M1 6h10"/></svg>
          www.vaneinquiries.co.nz
        </li>
      </ul>

      <ul class="contact__list">
        <li class="contact__item">
          <svg class="contact__icon" viewBox="0 0 12 12" fill="currentColor"><rect x="1" y="3" width="10" height="8" rx="1"/><rect x="3" y="1" width="6" height="3" rx="0.5"/></svg>
          +64 9 555 0142
        </li>
        <li class="contact__item">
          <svg class="contact__icon" viewBox="0 0 12 12" fill="none" stroke="currentColor" stroke-width="1.2"><rect x="3.2" y="0.8" width="5.6" height="10.4" rx="1"/><path d="M5.2 9.4h1.6"/></svg>
          +64 9 555 0187
        </li>
      </ul>
    </div>
  </article>

  <article class="card card--back">
    <div class="brand">
      <div class="brand__name">Halbrook &amp; Vane</div>
      <div class="brand__tagline">Investigations • Security • Intelligence</div>
    </div>
    <div class="holder">
      <div class="holder__name">Marcus Vane</div>
      <div class="holder__title">Director</div>
    </div>
  </article>

</body>
</html>
```